Infection control

to re-design website to include the benefits of powdered bleach packed in pre-measured sachets which when dissolved in water provides economy, efficacy and is safe to use with the use of costly packaging. We need new text outlining the benefits of the world's most commonly used disinfectant for major hospitals, institutions, pathology, military and disaster areas.

Translate design into coded website using CMS with the following features:
Mobile responsive using HTML 5/ CSS3 standards
Coded with SEO standards and with H1 tags for easy spidering and with Wordpress CMS with is page rank 9
Site migration
Email support
Updates

Target Market(s)

hospitals, institutions, pathology, military and disaster areas

Industry/Entity Type

Chemical Product

Number of Pages Required

4 page

Colors

Designer to choose colors to be used in the design.

Requirements
Must have
• factual information based on the efficiency of sodium hypochlorite (bleach) used for infection control. The many viruses, bacteria, pathogens etc which certain strengths of bleach eliminate upon contact.
• As tis is a redesign, existing pages including MSDS sheets to stay the same
Nice to have
• a new look and feel including current logos
Should not have
• incorrect info

```html
<!DOCTYPE html>
<html lang="en">
<head>
<meta charset="utf-8">
<title>Verdalis – Hospital Grade Infection Control</title>
<link href="https://fonts.googleapis.com/css2?family=Lato:ital,wght@0,400;0,700;1,400&family=Open+Sans:ital,wght@0,400;0,600;1,400&display=swap" rel="stylesheet">
<style>
:root{
  --green:#6cbd2a;
  --green-dark:#5aa81f;
  --ink:#111;
  --text:#555;
  --muted:#777;
  --nav:#555;
  --line:#dcdcdc;
  --footer-bg:#dddddd;
  --white:#fff;
}
*{margin:0;padding:0;box-sizing:border-box}
html,body{width:1200px;height:2469px;overflow:hidden;background:var(--white)}
body{position:relative;font-family:"Open Sans",Arial,sans-serif;color:var(--text)}
.abs{position:absolute}

/* header */
.site-header{left:0;top:0;width:1200px;height:102px;background:var(--white)}
.brand{left:115px;top:14px;display:flex;align-items:center;gap:10px}
.brand-mark{width:52px;height:52px;border-radius:50%;background:var(--green)}
.brand-name{font-family:"Lato",sans-serif;font-size:44px;font-weight:400;color:var(--green);line-height:1}
.brand-tag{left:118px;top:72px;font-family:"Open Sans",sans-serif;font-size:12.5px;color:#333;letter-spacing:.3px}
.main-nav a{position:absolute;top:46px;font-family:"Lato",sans-serif;font-size:20px;color:var(--nav);text-decoration:none}
.main-nav a.active{color:var(--green)}

/* hero */
.hero{left:0;top:102px;width:1200px;height:573px;background:linear-gradient(135deg,#4a4a4a 0%,#6b6b6b 45%,#3c3c3c 100%)}
.hero-title{left:120px;top:280px;width:640px;font-family:"Lato",sans-serif;font-weight:700;font-size:33px;line-height:41px;color:var(--white)}
.hero-dots{left:557px;top:547px;display:flex;gap:11px}
.hero-dots span{width:15px;height:15px;border-radius:50%;background:var(--white)}
.hero-dots span.current{background:transparent;border:2px solid var(--white)}
.hero-wave{left:0;top:570px}

/* welcome */
.welcome-photo{left:115px;top:661px;width:330px;height:330px;border-radius:50%;border:13px solid var(--green);background:radial-gradient(circle at 50% 40%,#e7d6c8,#b98a6c 60%,#5c7fa8)}
.welcome-title{left:467px;top:690px;font-family:"Lato",sans-serif;font-weight:700;font-size:36px;color:var(--ink)}
.welcome-text{left:469px;top:752px;width:600px;font-size:14.6px;line-height:26.2px;color:#444}

/* value pills */
.value{top:1062px;width:316px;height:125px;border:2px solid #dedede;border-radius:63px;background:var(--white)}
.value svg{position:absolute;left:38px;top:38px}
.value h3{position:absolute;left:94px;top:26px;font-family:"Lato",sans-serif;font-weight:400;font-size:22px;color:var(--ink)}
.value p{position:absolute;left:94px;top:60px;width:200px;font-size:14px;line-height:21px;color:#555}

/* features */
.features{left:0;top:1243px;width:1200px;height:559px;background:linear-gradient(90deg,#6cbf28,#79c93a 50%,#67b826)}
.features-notch{left:560px;top:1243px}
.features-title{left:0;top:1302px;width:1200px;text-align:center;font-family:"Lato",sans-serif;font-size:24px;font-weight:700;color:var(--white)}
.feature-card{top:1366px;width:230px;height:362px;border:1.5px solid rgba(255,255,255,.85);color:var(--white)}
.feature-card svg{position:absolute;top:20px}
.feature-card h3{position:absolute;top:88px;font-family:"Lato",sans-serif;font-weight:700;font-size:19px;line-height:23px}
.feature-card ul{position:absolute;list-style:none;font-size:14.5px;line-height:21.5px}

/* testimonials */
.testimonials-title{left:0;top:1855px;width:1200px;text-align:center;font-family:"Lato",sans-serif;font-weight:700;font-size:26px;color:var(--green)}
.quote-photo{left:285px;top:1913px;width:150px;height:150px;border-radius:50%;border:5px solid var(--green);background:radial-gradient(circle at 50% 45%,#d9b79c,#8c5a45 55%,#3e5a52)}
.quote-text{left:454px;top:1923px;width:560px;font-style:italic;font-size:18px;line-height:26.5px;color:var(--muted)}
.quote-author{left:456px;top:2023px;font-size:16px;color:#222}
.slider-arrow{top:1948px}

/* footer */
.site-footer{left:0;top:2183px;width:1200px;height:286px;background:var(--footer-bg)}
.partner-badge{left:166px;top:2247px;width:66px;height:66px;border-radius:50%;background:#b8b8b8}
.footer-col h4{position:absolute;top:2228px;font-family:"Lato",sans-serif;font-weight:400;font-size:19px;color:#444;white-space:nowrap}
.footer-col ul{position:absolute;top:2264px;list-style:none;font-size:13.5px;line-height:23.5px;color:#444}
.social{left:871px;top:2270px;display:flex;gap:5px}
.social span{width:36px;height:36px;border-radius:50%;background:var(--green)}
.footer-rule{left:115px;top:2411px;width:966px;height:1px;background:#b5b5b5}
.copyright{left:0;top:2425px;width:1200px;text-align:center;font-size:11.5px;color:#555}
</style>
</head>
<body>

<header class="site-header abs">
  <div class="brand abs"><span class="brand-mark"></span><span class="brand-name">Verdalis</span></div>
  <div class="brand-tag abs">Hospital Grade Infection Control</div>
  <nav class="main-nav">
    <a href="#" style="left:507px">About</a>
    <a href="#" class="active" style="left:599px">Products</a>
    <a href="#" style="left:714px">Downloads</a>
    <a href="#" style="left:849px">Media &amp; News</a>
    <a href="#" style="left:1009px">Contact</a>
  </nav>
</header>

<section class="hero abs" role="img" aria-label="Floor polishing machine cleaning a hard floor"></section>
<h1 class="hero-title abs">Our values are based on supplying quality products, on-time distribution and economy to the use</h1>
<div class="hero-dots abs"><span class="current"></span><span></span><span></span><span></span></div>
<svg class="hero-wave abs" width="1200" height="110" viewBox="0 0 1200 110" aria-hidden="true">
  <path d="M0 60 C300 12 700 0 1200 60 L1200 110 L0 110 Z" fill="#fff"/>
  <path d="M150 32 C420 5 760 -2 1200 58" fill="none" stroke="#6cbd2a" stroke-width="6"/>
  <path d="M0 62 C300 14 700 2 1200 62 L1200 110 L0 110 Z" fill="#fff"/>
</svg>

<section class="welcome">
  <div class="welcome-photo abs" role="img" aria-label="Two cleaning staff in uniforms with cleaning equipment"></div>
  <h2 class="welcome-title abs">Welcome to Our Website</h2>
  <p class="welcome-text abs">100% Australian owned and operated, Verdalis Bio-Chemical group has a proud history of supplying products to Australian and overseas markets for almost 3 decades. Formed and incorporated in 1986 in Victoria, Australia, Verdalis Bio-Chemical group continues to manufacture and distribute a wide range of bio chemical products. One of our most popular products is Puracide ®, a hospital grade disinfectant which we supply to major Australian hospitals, aged care facilities, schools, corrective services, pathology centres and the Australian Military as well as exporting to overseas markets.</p>
</section>

<section class="values">
  <div class="value abs" style="left:115px">
    <svg width="40" height="50" viewBox="0 0 40 50" aria-hidden="true"><path d="M30 12 C26 7 10 6 10 15 C10 24 30 21 30 32 C30 42 12 41 8 35" fill="none" stroke="#6cbd2a" stroke-width="6" stroke-linecap="round"/><line x1="20" y1="2" x2="20" y2="48" stroke="#6cbd2a" stroke-width="5"/></svg>
    <h3>Economy</h3><p>Ami a ultricies massa est sed nisl Class aptent taciti</p>
  </div>
  <div class="value abs" style="left:441px">
    <svg width="42" height="50" viewBox="0 0 42 50" aria-hidden="true"><path d="M6 48 C14 34 18 22 34 6" fill="none" stroke="#6cbd2a" stroke-width="4"/><path d="M20 26 C18 12 28 6 38 4 C38 16 32 26 20 26 Z" fill="#6cbd2a"/><path d="M14 36 C4 36 0 28 2 20 C10 20 16 26 14 36 Z" fill="#6cbd2a"/></svg>
    <h3>Efficacy</h3><p>Ami a ultricies massa est sed nisl Class aptent taciti</p>
  </div>
  <div class="value abs" style="left:764px">
    <svg width="40" height="50" viewBox="0 0 40 50" aria-hidden="true"><path d="M20 4 C28 18 34 26 34 34 A14 14 0 0 1 6 34 C6 26 12 18 20 4 Z" fill="#6cbd2a"/></svg>
    <h3>Safe to use</h3><p>Ami a ultricies massa est sed nisl Class aptent taciti</p>
  </div>
</section>

<section class="features-band">
  <div class="features abs" role="img" aria-label="Cleaner working in a hallway under a green tint"></div>
  <svg class="features-notch abs" width="80" height="22" viewBox="0 0 80 22" aria-hidden="true"><path d="M0 0 H80 L52 20 Q40 26 28 20 Z" fill="#fff"/><path d="M33 7 L40 12 L47 7" fill="none" stroke="#aaa" stroke-width="1.5"/></svg>
  <h2 class="features-title abs">FEATURES &amp; BENEFITS</h2>

  <div class="feature-card abs" style="left:117px">
    <svg style="left:34px" width="70" height="62" viewBox="0 0 70 62" aria-hidden="true"><g fill="#fff" stroke="#fff" stroke-width="3"><circle cx="24" cy="38" r="13"/><line x1="24" y1="16" x2="24" y2="60"/><line x1="2" y1="38" x2="46" y2="38"/><line x1="9" y1="23" x2="39" y2="53"/><line x1="39" y1="23" x2="9" y2="53"/><circle cx="53" cy="14" r="8"/><line x1="53" y1="1" x2="53" y2="27"/><line x1="40" y1="14" x2="66" y2="14"/><line x1="44" y1="5" x2="62" y2="23"/><line x1="62" y1="5" x2="44" y2="23"/></g></svg>
    <h3 style="left:34px">Infectious Wards</h3>
    <ul style="left:34px;top:121px;width:170px">
      <li>Wiping tables and bench tops</li><li>Mopping floors</li><li>Sanitising mattress covers</li><li>Disinfecting cutlery or other implements used by infectious patients</li><li>Operating Theatres</li>
    </ul>
  </div>

  <div class="feature-card abs" style="left:360px">
    <svg style="left:48px" width="52" height="52" viewBox="0 0 52 52" aria-hidden="true"><g fill="none" stroke="#fff" stroke-width="3"><path d="M4 16 L26 4 L48 16 Z"/><line x1="6" y1="20" x2="46" y2="20"/><line x1="12" y1="22" x2="12" y2="40"/><line x1="21" y1="22" x2="21" y2="40"/><line x1="31" y1="22" x2="31" y2="40"/><line x1="40" y1="22" x2="40" y2="40"/><line x1="4" y1="44" x2="48" y2="44"/><line x1="2" y1="49" x2="50" y2="49"/></g></svg>
    <h3 style="left:48px">Institutions</h3>
    <ul style="left:48px;top:121px"><li>Mopping floors</li><li>Walls</li></ul>
  </div>

  <div class="feature-card abs" style="left:604px">
    <svg style="left:30px" width="66" height="52" viewBox="0 0 66 52" aria-hidden="true"><g fill="none" stroke="#fff" stroke-width="3"><line x1="2" y1="4" x2="64" y2="4"/><rect x="8" y="4" width="10" height="36" rx="5"/><rect x="28" y="4" width="10" height="36" rx="5"/><rect x="48" y="4" width="10" height="36" rx="5"/><line x1="2" y1="48" x2="64" y2="48"/></g><g fill="#fff"><rect x="10" y="22" width="6" height="16"/><rect x="30" y="22" width="6" height="16"/><rect x="50" y="22" width="6" height="16"/></g></svg>
    <h3 style="left:26px;width:180px">Pathology Laboratories</h3>
    <ul style="left:26px;top:144px"><li>Bench tops</li><li>Floors</li><li>Walls</li></ul>
  </div>

  <div class="feature-card abs" style="left:851px">
    <svg style="left:38px" width="62" height="56" viewBox="0 0 62 56" aria-hidden="true"><path d="M2 54 L24 20 H38 L60 54 Z" fill="#fff"/><g stroke="#fff" stroke-width="3" fill="none"><line x1="31" y1="16" x2="31" y2="2"/><line x1="24" y1="14" x2="16" y2="4"/><line x1="38" y1="14" x2="46" y2="4"/></g><path d="M31 34 L34 46 H28 Z" fill="#6cbd2a"/></svg>
    <h3 style="left:32px">Disaster Areas</h3>
    <ul style="left:32px;top:121px"><li>Etiam eu urna</li><li>Sed porta</li><li>Suspendisse quam</li><li>Leo molestie</li></ul>
  </div>
</section>

<section class="testimonials">
  <h2 class="testimonials-title abs">TESTIMONIALS</h2>
  <svg class="slider-arrow abs" style="left:150px" width="22" height="36" viewBox="0 0 22 36" aria-label="Previous"><path d="M18 3 L4 18 L18 33" fill="none" stroke="#888" stroke-width="4"/></svg>
  <svg class="slider-arrow abs" style="left:1057px" width="22" height="36" viewBox="0 0 22 36" aria-label="Next"><path d="M4 3 L18 18 L4 33" fill="none" stroke="#888" stroke-width="4"/></svg>
  <div class="quote-photo abs" role="img" aria-label="Portrait of a smiling customer"></div>
  <blockquote class="quote-text abs">Vivamus porttitor purus nisi eleifend libero a tempus libero lectus feugiat felis Morbi diam mauris viverra in gravida eu mattis in ante Morbi eget arcu Morbi porta libero id ullamcorper nonum</blockquote>
  <p class="quote-author abs">By Author Name</p>
</section>

<footer class="site-footer abs"></footer>
<div class="partner-badge abs" role="img" aria-label="Partner badge"></div>
<div class="footer-col">
  <h4 style="left:366px">QUICK LINKS</h4>
  <ul style="left:366px"><li>About Us</li><li>Our Products</li><li>Media &amp; news</li><li>Contact Us</li></ul>
</div>
<div class="footer-col">
  <h4 style="left:594px">CONTACT US</h4>
  <ul style="left:594px"><li>Phone: 1300 555 012</li><li>Fax Direct: 1300 555 013</li><li>info@verdalisgroup.com.au</li><li>Sitemap</li></ul>
</div>
<div class="footer-col">
  <h4 style="left:870px">GET IN TOUCH</h4>
</div>
<div class="social abs" aria-label="Social links"><span></span><span></span><span></span><span></span><span></span></div>
<div class="footer-rule abs"></div>
<p class="copyright abs">© 2018 Company Name&nbsp; All right reserved</p>

</body>
</html>
```